OpenHarbor Yoga Website Design

Business Logo - attached
5 pages being:
Home
About
Classes
Blog
Contact

Would like Scrolling webpage and yoga symbols to be used.

Must have's being:
Easy to navigate, Text needs to be able to be edited/updated, Enquire Now Links, More Information Links, be a secure site, SEO,

Please refer to attached document for the information for the body of the website.

Target Market(s)

Educators, Community Service, Health and Wellbeing, Mental Health

Industry/Entity Type

Yoga

Coding

Coded - Design and coding required

Number of Pages Required

5+ page

Font styles to use
Other font styles liked:
• Bella Bold BC

Colors
0094D4
00A9DD
6FCCEA
C7EBF8
E9F6FB
6B429C
8869AF
B7A5CE
E3DAEB
F3F0F8

Requirements
Must have
• Easy to navigate, Text needs to be able to be edited/updated, Enquire Now Links, More Information Links, be a secure site, SEO,
Nice to have
• Scrolling webpage, yoga symbols

```html
<!DOCTYPE html>
<html lang="en">
<head>
<meta charset="utf-8">
<title>OpenHarbor Yoga</title>
<link href="https://fonts.googleapis.com/css2?family=Bebas+Neue&family=Lato:wght@400;700&family=Poppins:wght@400;500;600;700&display=swap" rel="stylesheet">
<style>
:root{
  --purple:#5a17c8;
  --purple-light:#b48ef2;
  --ink:#1d1d1f;
  --body:#444;
  --lavender:#f7f5fa;
  --black:#000;
  --white:#fff;
}
*{margin:0;padding:0;box-sizing:border-box}
html,body{width:1200px;height:3150px;overflow:hidden;background:var(--white)}
body{position:relative;font-family:'Lato',sans-serif;color:var(--body)}
.abs{position:absolute}
.display{font-family:'Bebas Neue',sans-serif;letter-spacing:.5px}

/* header */
.site-header{left:0;top:0;width:1200px;height:86px;background:var(--white);z-index:3}
.brand{left:98px;top:0;width:143px;height:160px;border-radius:0 0 72px 72px;background:var(--white);box-shadow:0 6px 0 #8a8a8a;z-index:4;display:flex;align-items:center;justify-content:center;text-align:center;font-family:'Poppins',sans-serif;font-weight:600;font-size:17px;line-height:1.2;color:var(--purple)}
.nav{right:99px;top:20px;display:flex;align-items:center;gap:37px;font-family:'Poppins',sans-serif;font-size:16px;color:var(--ink)}
.nav .active{color:var(--purple);text-decoration:underline;text-underline-offset:6px}
.btn{display:inline-flex;align-items:center;justify-content:center;border-radius:24px;font-family:'Poppins',sans-serif;font-weight:600;font-size:16px;color:var(--white);background:linear-gradient(90deg,var(--purple),var(--purple-light))}
.nav .btn{width:137px;height:46px;margin-left:0}

/* hero */
.hero{left:0;top:86px;width:1200px;height:600px;background:radial-gradient(ellipse at 70% 20%,#3a3f9a 0%,#1c1f5a 35%,transparent 60%),linear-gradient(180deg,#111645 0%,#3b3a8c 40%,#c06aa0 62%,#9fb7c9 78%,#3a3040 100%)}
.hero-title{left:99px;top:290px;font-size:58px;color:var(--white)}
.hero-text{left:99px;top:355px;width:460px;font-size:15.5px;line-height:31px;color:var(--white)}
.hero-btn{left:99px;top:429px;width:137px;height:47px;border-radius:24px;background:var(--white);color:var(--purple);font-family:'Poppins',sans-serif;font-weight:600;font-size:16px;display:flex;align-items:center;justify-content:center}
.arrow{top:375px;width:22px;height:22px}

/* about */
.about-photo{left:98px;top:764px;width:495px;height:464px;background:radial-gradient(circle at 50% 70%,#f6c060 0%,#d98a2c 40%,#5a3520 100%)}
.section-title{font-size:34px;color:var(--ink)}
.section-title span{color:var(--purple)}
.rule{height:3px;background:var(--purple)}
.about-title{left:635px;top:757px}
.about-text{left:635px;top:822px;width:470px;font-size:15px;line-height:31px}
.about-btn{left:635px;top:1186px;width:137px;height:47px}

/* benefits */
.benefits{left:0;top:1315px;width:1200px;height:1396px;background:var(--lavender)}
.benefits-title{left:0;width:1200px;top:1366px;text-align:center}
.benefits-intro{left:150px;width:900px;top:1435px;text-align:center;font-size:15.5px;line-height:30px;color:var(--ink)}
.photo{width:483px;height:303px}
.badge{width:110px;height:110px}
.item-title{font-family:'Poppins',sans-serif;font-weight:500;font-size:21px;color:var(--ink)}
.list{list-style:none;font-size:15.5px;line-height:34px;color:var(--ink)}
.list li{position:relative;padding-left:22px}
.list li::before{content:"";position:absolute;left:0;top:13px;width:10px;height:10px;border-radius:50%;background:var(--purple)}

/* footer */
.site-footer{left:0;top:2711px;width:1200px;height:439px;background:var(--black);color:var(--white)}
.foot-h{font-family:'Poppins',sans-serif;font-weight:600;font-size:27px;color:var(--white)}
.links{list-style:none;font-family:'Poppins',sans-serif;font-weight:600;font-size:14px;line-height:31px}
.links li{display:flex;align-items:center;gap:12px}
.vdiv{width:0;border-left:1px dashed #888}
.hdiv{height:0;border-top:1px dashed #888}
.contact-label{font-family:'Poppins',sans-serif;font-size:18px}
.contact-val{font-family:'Poppins',sans-serif;font-size:15.5px}
.field{left:716px;width:352px;height:40px;border:1px solid var(--white);border-radius:3px;padding:10px 12px;font-family:'Poppins',sans-serif;font-size:14px}
.submit{left:716px;top:2967px;width:352px;height:38px;background:var(--purple);font-family:'Poppins',sans-serif;font-weight:600;font-size:17px;display:flex;align-items:center;justify-content:center}
.social{top:3014px;width:30px;height:30px;border:1px solid var(--white);border-radius:50%}
.copyright{left:0;width:1200px;top:3110px;text-align:center;font-family:'Poppins',sans-serif;font-size:14px}
</style>
</head>
<body>

<header class="abs site-header">
  <div class="abs brand">OpenHarbor<br>Yoga</div>
  <nav class="abs nav">
    <span class="active">Home</span><span>About</span><span>Classes</span><span>Blog</span>
    <span class="btn">Contact Us</span>
  </nav>
</header>

<section class="abs hero" role="img" aria-label="Person sitting cross-legged with raised joined hands under a starry aurora sky at dusk"></section>
<svg class="abs arrow" style="left:44px" viewBox="0 0 22 22"><circle cx="11" cy="11" r="10" fill="none" stroke="#fff" stroke-width="1.3"/><path d="M12.5 7l-4 4 4 4" fill="none" stroke="#fff" stroke-width="1.3"/></svg>
<svg class="abs arrow" style="left:1134px" viewBox="0 0 22 22"><circle cx="11" cy="11" r="10" fill="none" stroke="#fff" stroke-width="1.3"/><path d="M9.5 7l4 4-4 4" fill="none" stroke="#fff" stroke-width="1.3"/></svg>
<h1 class="abs display hero-title">WELCOME TO OPENHARBOR YOGA</h1>
<p class="abs hero-text">OpenHarbor Yoga believe that you are never too young to benefit from and fall in love with yoga.</p>
<a class="abs hero-btn">Enquire Now</a>

<div class="abs about-photo" role="img" aria-label="Silhouette of a person meditating against an orange sunset"></div>
<h2 class="abs display section-title about-title"><span>ABOUT</span> US</h2>
<div class="abs rule" style="left:635px;top:802px;width:71px"></div>
<p class="abs about-text">Hi and welcome to OpenHarbor Yoga!<br>My name is Clara, and I am the creator &amp; facilitator of OpenHarbor Yoga. With the increasing numbers of youth mental health, I have started OpenHarbor Yoga wanting to assist children and teens with their mental health for life, with the magic of yoga.I had always wanted to teach children, but had never found the right platform to do so... That was until I found yoga! I genuinely believe the practice of yoga and mindfulness especially at a young age can offer life-long tools to kids and teens such as dealing with their emotions, developing resilience, self-awareness, respect and confidence in a positive and fun environment.</p>
<a class="abs btn about-btn">Read More</a>

<section class="abs benefits"></section>
<h2 class="abs display section-title benefits-title">BENEFITS OF <span>YOGA...</span></h2>
<div class="abs rule" style="left:580px;top:1422px;width:40px"></div>
<p class="abs benefits-intro">The benefits of yoga can last a lifetime. It is my aim &amp; passion to introduce yoga to kids of all ages and backgrounds so that they can not only experience the benefits of yoga but fall in love with the practice.<br>Yoga benefits include:</p>

<div class="abs photo" style="left:98px;top:1566px;background:linear-gradient(135deg,#f3ede6,#d9c9b6 60%,#8a7a68)" role="img" aria-label="Woman meditating cross-legged in a bright living room"></div>
<svg class="abs badge" style="left:521px;top:1662px" viewBox="0 0 110 110" role="img" aria-label="Seated meditation icon"><circle cx="55" cy="55" r="49" fill="#fff" stroke="#5a17c8" stroke-width="10"/><circle cx="55" cy="55" r="24" fill="#ece5f8"/></svg>
<h3 class="abs item-title" style="left:660px;top:1558px">Healthy bodies</h3>
<ul class="abs list" style="left:660px;top:1597px;width:440px">
  <li>Develops strong, flexible and healthy bodies</li>
  <li>Promotes spinal alignment and good posture</li>
  <li>Builds energy and stamina</li>
  <li>Improves internal physical function - organs, digestion, elimination, circulation, and blood flow.</li>
  <li>Helps breathing and lung capacity</li>
  <li>Teaches the enjoyment of movement</li>
  <li>Works the ‘whole’ body</li>
</ul>

<h3 class="abs item-title" style="left:98px;top:1935px">Healthy minds</h3>
<ul class="abs list" style="left:98px;top:1974px;width:440px">
  <li>Cultivates confidence and self-esteem</li>
  <li>Develops concentration and attention</li>
  <li>Clears the mind for better clarity and decision making</li>
  <li>Helps relax and sleep better</li>
  <li>Calms the nervous system</li>
  <li>Learns to cope with stressful situations</li>
</ul>
<div class="abs photo" style="left:618px;top:1942px;background:linear-gradient(135deg,#c9c39a,#8f8a5a 50%,#5e5a3a)" role="img" aria-label="Woman breathing calmly outdoors with hands on chest"></div>
<svg class="abs badge" style="left:566px;top:2039px" viewBox="0 0 110 110" role="img" aria-label="Mindful meditation icon"><circle cx="55" cy="55" r="49" fill="#fff" stroke="#5a17c8" stroke-width="10"/><circle cx="55" cy="55" r="24" fill="#ece5f8"/></svg>

<div class="abs photo" style="left:98px;top:2320px;background:linear-gradient(180deg,#d8e2e6,#9fb6bd 45%,#c9c2b4 80%,#b8ad9c)" role="img" aria-label="Person in tree pose on a beach"></div>
<svg class="abs badge" style="left:521px;top:2417px" viewBox="0 0 110 110" role="img" aria-label="Lotus meditation icon"><circle cx="55" cy="55" r="49" fill="#fff" stroke="#5a17c8" stroke-width="10"/><circle cx="55" cy="55" r="24" fill="#ece5f8"/></svg>
<h3 class="abs item-title" style="left:660px;top:2313px">Healthy spirits</h3>
<ul class="abs list" style="left:660px;top:2352px;width:440px">
  <li>Fosters creativity, expression and imagination</li>
  <li>Cultivates kindness to themselves and others</li>
  <li>Cultivates respect for self and others</li>
  <li>Builds balance and inner quiet</li>
  <li>Builds inner strength and resilience</li>
  <li>Teaches self-awareness</li>
  <li>Focuses on positive self-talk</li>
</ul>

<footer class="abs site-footer"></footer>
<h4 class="abs foot-h" style="left:98px;top:2758px">Quick Links</h4>
<ul class="abs links" style="left:98px;top:2801px;color:#fff">
  <li><svg width="14" height="14" viewBox="0 0 14 14"><path d="M1 7h11M7.5 2.5L12 7l-4.5 4.5" fill="none" stroke="#fff" stroke-width="2"/></svg>Home</li>
  <li><svg width="14" height="14" viewBox="0 0 14 14"><path d="M1 7h11M7.5 2.5L12 7l-4.5 4.5" fill="none" stroke="#fff" stroke-width="2"/></svg>About</li>
  <li><svg width="14" height="14" viewBox="0 0 14 14"><path d="M1 7h11M7.5 2.5L12 7l-4.5 4.5" fill="none" stroke="#fff" stroke-width="2"/></svg>Classes</li>
  <li><svg width="14" height="14" viewBox="0 0 14 14"><path d="M1 7h11M7.5 2.5L12 7l-4.5 4.5" fill="none" stroke="#fff" stroke-width="2"/></svg>Blog</li>
  <li><svg width="14" height="14" viewBox="0 0 14 14"><path d="M1 7h11M7.5 2.5L12 7l-4.5 4.5" fill="none" stroke="#fff" stroke-width="2"/></svg>More Information</li>
  <li><svg width="14" height="14" viewBox="0 0 14 14"><path d="M1 7h11M7.5 2.5L12 7l-4.5 4.5" fill="none" stroke="#fff" stroke-width="2"/></svg>Contact</li>
</ul>
<div class="abs social" style="left:98px"></div>
<div class="abs social" style="left:144px"></div>
<div class="abs vdiv" style="left:302px;top:2794px;height:240px"></div>
<div class="abs vdiv" style="left:670px;top:2794px;height:240px"></div>

<h4 class="abs foot-h" style="left:355px;top:2758px">Contact Details</h4>
<svg class="abs" style="left:355px;top:2811px" width="36" height="36" viewBox="0 0 36 36"><circle cx="18" cy="18" r="17" fill="none" stroke="#fff"/><path d="M13 11l3 0 1.5 4-2 1.5a9 9 0 0 0 4 4l1.5-2 4 1.5v3c-7 1-13-5-12-12z" fill="#fff"/></svg>
<div class="abs contact-label" style="left:400px;top:2808px">Phone;</div>
<div class="abs contact-val" style="left:400px;top:2840px">0400 123 456</div>
<div class="abs hdiv" style="left:355px;top:2876px;width:241px"></div>
<svg class="abs" style="left:355px;top:2893px" width="36" height="36" viewBox="0 0 36 36"><circle cx="18" cy="18" r="17" fill="none" stroke="#fff"/><rect x="11" y="13" width="14" height="10" fill="#fff"/><path d="M11 13l7 5 7-5" fill="none" stroke="#000" stroke-width="1.2"/></svg>
<div class="abs contact-label" style="left:400px;top:2889px">Email:</div>
<div class="abs contact-val" style="left:404px;top:2921px">hello@openharboryoga.example</div>
<div class="abs hdiv" style="left:355px;top:2958px;width:241px"></div>
<svg class="abs" style="left:355px;top:2976px" width="36" height="36" viewBox="0 0 36 36"><circle cx="18" cy="18" r="17" fill="none" stroke="#fff"/><path d="M18 26s-5-6-5-10a5 5 0 0 1 10 0c0 4-5 10-5 10z" fill="#fff"/><circle cx="18" cy="16" r="1.8" fill="#000"/></svg>
<div class="abs contact-label" style="left:400px;top:2982px">Address:</div>
<div class="abs contact-val" style="left:400px;top:3014px">Harbourvale, Victoria Australia 3999</div>
<div class="abs contact-val" style="left:400px;top:3044px">ABN:&nbsp; 00 000 000 000</div>

<h4 class="abs foot-h" style="left:716px;top:2758px">Contact Me</h4>
<div class="abs field" style="top:2808px">Name:</div>
<div class="abs field" style="top:2861px">Email:</div>
<div class="abs field" style="top:2914px">Address:</div>
<div class="abs submit">Submit Now</div>

<div class="abs hdiv" style="left:98px;top:3095px;width:1003px;border-top:1px solid #aaa"></div>
<p class="abs copyright">Copyrights@2023.OpenHarbor Yoga.All Rights Reserved</p>

</body>
</html>
```